My Pebble Porch Path Blog Re-Do Launch

I need a blog makeover. Someone started for me and they sold their company. The blog is primarily spiritual/inspirational. I would eventually like to monetize and launch some ebooks and/or other products. I am open to suggestions. I am learning as we go along, so please keep that in mind. The final design should be warm and welcoming. I am open to suggestions. I am looking to build a relationship.

Target Market(s)

women, moms, females with chronic health issues, moms of special needs kids, those who need encouragement

Industry/Entity Type

Religious

Number of Pages Required

4 page

Font styles to use
Sans Serif

Colors
eddcec
fdf9cf
ffffff

Requirements
Must have
• I would like my main page to have a short about section, relevant posts, recent posts, and archive posts. The main page should also have a place to subscribe as well a search feature.
Nice to have
• Buttons (grab my button), blogs I follow, e-cart capabilities

```html
<!DOCTYPE html>
<html lang="en">
<head>
<meta charset="utf-8">
<title>My Pebble Porch Path</title>
<link href="https://fonts.googleapis.com/css2?family=Roboto+Condensed:wght@400;700&family=Open+Sans:ital,wght@0,400;0,600;1,400&display=swap" rel="stylesheet">
<style>
:root{
  --pink:#eddcec;
  --pink-deep:#c99bc7;
  --cream:#fdf9cf;
  --white:#ffffff;
  --ink:#2b2b2b;
  --text:#6d6d6d;
  --meta:#8a8a8a;
  --rule:#e2e2e2;
  --footer:#2f2f2f;
  --head:"Roboto Condensed",sans-serif;
  --body:"Open Sans",sans-serif;
}
*{box-sizing:border-box;margin:0;padding:0}
html,body{width:1200px;height:2187px;overflow:hidden;background:var(--white)}
body{position:relative;font-family:var(--body);color:var(--text)}
.top-strip{position:absolute;top:0;left:0;width:1200px;height:4px;background:linear-gradient(90deg,#f3d9c8,#e7c6e6,#f3e7c4)}
.site-header{position:absolute;top:4px;left:0;width:1200px;height:86px}
.brand{position:absolute;left:98px;top:24px;display:flex;align-items:center;gap:12px;font-family:var(--head);font-weight:700;font-size:17px;color:var(--ink);text-transform:uppercase}
.brand-mark{width:60px;height:60px;background:var(--pink);border-radius:4px}
.main-nav{position:absolute;left:437px;top:34px;display:flex;gap:0;font-family:var(--head);font-weight:700;font-size:13px;text-transform:uppercase;color:var(--ink)}
.main-nav a{color:inherit;text-decoration:none;margin-right:30px}
.main-nav a.active{color:var(--pink-deep)}
.nav-search{position:absolute;left:913px;top:34px}
.cart{position:absolute;left:944px;top:24px;display:flex;gap:10px;align-items:flex-start}
.cart-label{font-family:var(--head);font-weight:700;font-size:13px;color:var(--ink);line-height:16px}
.cart-label span{display:block;font-family:var(--body);font-weight:400;font-size:11px;color:var(--meta)}
.hero{position:absolute;top:90px;left:0;width:1200px;height:435px;background:linear-gradient(180deg,#b9a590 0%,#e6d2b4 45%,#f4e7c9 65%,#6b5a45 88%,#1d1812 100%)}
.hero-title{position:absolute;left:98px;top:112px;font-family:var(--head);font-weight:700;font-size:38px;color:#141414;text-transform:uppercase}
.hero-text{position:absolute;left:98px;top:166px;width:510px;font-style:italic;font-size:12.5px;line-height:22px;color:#1e1e1e}
.hero .btn{position:absolute;left:98px;top:250px}
.hero-arrow{position:absolute;top:206px}
.hero-dots{position:absolute;left:565px;top:402px;display:flex;gap:6px}
.hero-dots span{width:14px;height:14px;border-radius:50%;border:2px solid #fff;background:rgba(0,0,0,.35)}
.hero-dots span.on{background:var(--pink)}
.btn{display:inline-block;width:114px;height:38px;line-height:38px;text-align:center;font-family:var(--head);font-weight:700;font-size:13px;color:var(--ink);text-transform:uppercase;background:linear-gradient(180deg,#f6ebf5,var(--pink));border:1px solid #dcc2da;border-radius:2px;box-shadow:0 2px 3px rgba(0,0,0,.12)}
.section-title{font-family:var(--head);font-weight:700;font-size:21px;color:var(--ink);text-transform:uppercase;padding-bottom:14px;border-bottom:3px double var(--rule)}
.posts{position:absolute;left:98px;top:556px;width:605px}
.post{display:flex;gap:25px;height:234px;padding-top:71px;border-bottom:1px solid var(--rule)}
.post:first-of-type{margin-top:0}
.post-list .post{padding-top:22px}
.post-list{margin-top:14px}
.thumb{flex:none;width:224px;height:190px;border:1px solid #d6d6d6;padding:3px;background:#fff}
.thumb div{width:100%;height:100%}
.post-title{font-family:var(--head);font-weight:700;font-size:15px;color:var(--ink);text-transform:uppercase;margin-top:4px}
.meta{font-family:var(--head);font-size:11.5px;color:var(--meta);margin:8px 0 12px;display:flex;align-items:center;gap:6px}
.meta i{font-style:normal;color:#bbb}
.excerpt{font-size:12px;line-height:22px;color:var(--text)}
.post .btn{margin-top:14px}
.pager{position:absolute;left:98px;top:2037px;display:flex;gap:10px;font-size:11px}
.pager span{min-width:25px;height:25px;line-height:23px;text-align:center;border:1px solid #d8d8d8;color:var(--ink);padding:0 7px;box-shadow:0 1px 2px rgba(0,0,0,.08)}
.pager span.on{background:var(--pink);color:#fff;border-color:var(--pink)}
.pager .wide{width:47px}
.sidebar{position:absolute;left:735px;top:556px;width:367px}
.search-box{margin-top:16px;height:45px;border:2px solid #e0e0e0;display:flex;align-items:center;justify-content:space-between;padding:0 16px;font-size:11px;color:#9a9a9a;text-transform:uppercase}
.widget{margin-top:0}
.divider{height:1px;background:var(--rule);margin:24px 0 28px}
.side-item{display:flex;gap:18px;padding:16px 0 14px;border-bottom:1px solid var(--rule)}
.side-item .s-thumb{flex:none;width:105px;height:93px;border:1px solid #d6d6d6;padding:2px}
.side-item .s-thumb div{width:100%;height:100%}
.side-title{font-family:var(--head);font-weight:700;font-size:13px;color:var(--ink);text-transform:uppercase;text-decoration:underline}
.side-item .meta{margin:7px 0 6px;font-size:11px}
.side-text{font-size:11.5px;line-height:17px}
.archive-item{display:flex;gap:18px;align-items:flex-start;height:88.5px;padding-top:14px;border-bottom:1px solid var(--rule)}
.archive-item .a-thumb{flex:none;width:76px;height:58px;border:1px solid #d6d6d6;padding:2px}
.archive-item .a-thumb div{width:100%;height:100%}
.archive-item .meta{margin:7px 0 0;font-size:11px}
.view-more{text-align:right;font-family:var(--head);font-weight:700;font-size:11.5px;color:var(--pink-deep);text-transform:uppercase;margin-top:22px}
.view-more u{text-decoration:underline}
.newsletter{margin-top:16px;height:160px;background:linear-gradient(180deg,var(--cream),#efe6b8);border:1px solid #e7dfb4;padding:18px 20px}
.field{height:34px;background:#fff;border:1px solid #eee;font-size:11.5px;color:#888;padding:0 12px;line-height:34px;margin-bottom:12px;text-transform:uppercase}
.newsletter .btn{width:96px;height:33px;line-height:31px;font-size:12px}
.site-footer{position:absolute;top:2094px;left:0;width:1200px;height:93px;background:var(--footer);color:#fff}
.foot-links{position:absolute;left:98px;top:24px;font-size:12px}
.foot-links span{margin:0 6px;color:#aaa}
.copyright{position:absolute;left:98px;top:48px;font-size:11.5px}
.social{position:absolute;left:917px;top:23px;display:flex;gap:12px}
.social span{width:40px;height:40px;border:2px solid #fff;border-radius:50%}
</style>
</head>
<body>
<div class="top-strip"></div>

<header class="site-header">
  <div class="brand"><span class="brand-mark"></span>My Pebble Porch Path</div>
  <nav class="main-nav">
    <a class="active" href="#">&#8962; Home</a><a href="#">About Us</a><a href="#">Services</a><a href="#">Blog</a><a href="#">Events</a><a href="#">Contact Us</a>
  </nav>
  <svg class="nav-search" width="16" height="16" viewBox="0 0 16 16"><circle cx="6.5" cy="6.5" r="5" fill="none" stroke="#999" stroke-width="2"/><line x1="10" y1="10" x2="14.5" y2="14.5" stroke="#999" stroke-width="2"/></svg>
  <div class="cart">
    <svg width="34" height="30" viewBox="0 0 34 30"><path d="M2 4h6l4 16h16l4-12H10" fill="none" stroke="#e9b24f" stroke-width="2.5"/><circle cx="14" cy="26" r="2.5" fill="#e9b24f"/><circle cx="26" cy="26" r="2.5" fill="#e9b24f"/></svg>
    <div class="cart-label">My Cart<span>0 item(s) | $ 0.00 &#9662;</span></div>
  </div>
</header>

<section class="hero" role="img" aria-label="Sunset sky over tall grass with a silhouetted cross">
  <h1 class="hero-title">My Pebble Porch Path</h1>
  <p class="hero-text">Et harum quidem rerum facilis est et expedita distinctio. Nam libero tempore, cum soluta nobis est eligendi optio cumque nihil impedit quo minus id quod maxime placeat possimus voluptas assumenda est, omnis dolor repellendus.</p>
  <span class="btn">Read More &gt;&gt;</span>
  <svg class="hero-arrow" style="left:36px" width="16" height="26" viewBox="0 0 16 26"><path d="M13 2 3 13l10 11" fill="none" stroke="#fff" stroke-width="2.5"/></svg>
  <svg class="hero-arrow" style="left:1147px" width="16" height="26" viewBox="0 0 16 26"><path d="M3 2l10 11L3 24" fill="none" stroke="#fff" stroke-width="2.5"/></svg>
  <div class="hero-dots"><span class="on"></span><span></span><span></span><span></span></div>
</section>

<main class="posts">
  <h2 class="section-title">Relevant Posts</h2>
  <div class="post-list">
    <article class="post">
      <div class="thumb"><div role="img" aria-label="Lit candle beside an open book" style="background:linear-gradient(135deg,#f3c46a,#a7652a 55%,#3d2310)"></div></div>
      <div><h3 class="post-title">Nemo enim ipsam voluptatem quia voluptas sit asp</h3>
      <div class="meta">&#128197; 25/11/2015 <i>|</i> &#128100; John Doe <i>|</i> &#128172; 0 Comments</div>
      <p class="excerpt">Nam libero tempore, cum soluta nobis est eligendi optio cumq ue nihil impedit quo minus id quod maxime placeat facere poss imus, omnis voluptas assumenda es omnis dolor repellendus. Temporibus autem quibusdam et aut ..</p>
      <span class="btn">Read More &gt;&gt;</span></div>
    </article>
    <article class="post">
      <div class="thumb"><div role="img" aria-label="Woman bowing her head in prayer" style="background:linear-gradient(135deg,#e9e4df,#a89a8c 50%,#4a3a30)"></div></div>
      <div><h3 class="post-title">Nemo enim ipsam voluptatem quia voluptas sit asp</h3>
      <div class="meta">&#128197; 25/11/2015 <i>|</i> &#128100; John Doe <i>|</i> &#128172; 0 Comments</div>
      <p class="excerpt">Nam libero tempore, cum soluta nobis est eligendi optio cumq ue nihil impedit quo minus id quod maxime placeat facere poss imus, omnis voluptas assumenda es omnis dolor repellendus. Temporibus autem quibusdam et aut ..</p>
      <span class="btn">Read More &gt;&gt;</span></div>
    </article>
    <article class="post">
      <div class="thumb"><div role="img" aria-label="Cross resting on a closed bible" style="background:linear-gradient(135deg,#d9cbb6,#8c4a2a 50%,#3a2418)"></div></div>
      <div><h3 class="post-title">Nemo enim ipsam voluptatem quia voluptas sit asp</h3>
      <div class="meta">&#128197; 25/11/2015 <i>|</i> &#128100; John Doe <i>|</i> &#128172; 0 Comments</div>
      <p class="excerpt">Nam libero tempore, cum soluta nobis est eligendi optio cumq ue nihil impedit quo minus id quod maxime placeat facere poss imus, omnis voluptas assumenda es omnis dolor repellendus. Temporibus autem quibusdam et aut ..</p>
      <span class="btn">Read More &gt;&gt;</span></div>
    </article>
    <article class="post">
      <div class="thumb"><div role="img" aria-label="Open hands beneath a glowing cross" style="background:linear-gradient(180deg,#f1ebf0,#f6d6b0 55%,#eeb27a)"></div></div>
      <div><h3 class="post-title">Nemo enim ipsam voluptatem quia voluptas sit asp</h3>
      <div class="meta">&#128197; 25/11/2015 <i>|</i> &#128100; John Doe <i>|</i> &#128172; 0 Comments</div>
      <p class="excerpt">Nam libero tempore, cum soluta nobis est eligendi optio cumq ue nihil impedit quo minus id quod maxime placeat facere poss imus, omnis voluptas assumenda es omnis dolor repellendus. Temporibus autem quibusdam et aut ..</p>
      <span class="btn">Read More &gt;&gt;</span></div>
    </article>
    <article class="post">
      <div class="thumb"><div role="img" aria-label="Person kneeling before a cross at sunset" style="background:linear-gradient(180deg,#c9506a,#e07a5a 45%,#f0b45a 65%,#1a1010 85%)"></div></div>
      <div><h3 class="post-title">Nemo enim ipsam voluptatem quia voluptas sit asp</h3>
      <div class="meta">&#128197; 25/11/2015 <i>|</i> &#128100; John Doe <i>|</i> &#128172; 0 Comments</div>
      <p class="excerpt">Nam libero tempore, cum soluta nobis est eligendi optio cumq ue nihil impedit quo minus id quod maxime placeat facere poss imus, omnis voluptas assumenda es omnis dolor repellendus. Temporibus autem quibusdam et aut ..</p>
      <span class="btn">Read More &gt;&gt;</span></div>
    </article>
    <article class="post">
      <div class="thumb"><div role="img" aria-label="Person kneeling by a cross at the seashore" style="background:linear-gradient(180deg,#6d9bc8,#b6c9d6 50%,#d9b28a 70%,#4a3a30)"></div></div>
      <div><h3 class="post-title">Nemo enim ipsam voluptatem quia voluptas sit asp</h3>
      <div class="meta">&#128197; 25/11/2015 <i>|</i> &#128100; John Doe <i>|</i> &#128172; 0 Comments</div>
      <p class="excerpt">Nam libero tempore, cum soluta nobis est eligendi optio cumq ue nihil impedit quo minus id quod maxime placeat facere poss imus, omnis voluptas assumenda es omnis dolor repellendus. Temporibus autem quibusdam et aut ..</p>
      <span class="btn">Read More &gt;&gt;</span></div>
    </article>
  </div>
</main>

<nav class="pager">
  <span class="wide">Prev</span><span class="on">1</span><span>2</span><span>3</span><span>4</span><span>5</span><span>6</span><span>..</span><span>22</span><span class="wide">Next</span>
</nav>

<aside class="sidebar">
  <h2 class="section-title" style="border-bottom:none;padding-bottom:0">Search</h2>
  <div class="search-box">Search
    <svg width="16" height="16" viewBox="0 0 16 16"><circle cx="6.5" cy="6.5" r="5" fill="none" stroke="#999" stroke-width="2"/><line x1="10" y1="10" x2="14.5" y2="14.5" stroke="#999" stroke-width="2"/></svg>
  </div>
  <div class="divider"></div>

  <h2 class="section-title">Recent Posts</h2>
  <div class="side-item">
    <div class="s-thumb"><div role="img" aria-label="Figure with raised arms at golden sunset" style="background:linear-gradient(180deg,#f2b24a,#9a4a1e 60%,#2a1408)"></div></div>
    <div><div class="side-title">Finibus bonorum et malorum</div>
    <div class="meta">&#128197; 25/11/2015 <i>|</i> &#128100; John <i>|</i> &#128172; 0 Comments</div>
    <p class="side-text">Nam libero tempore, cum soluta nobis est eligendi optio cumque nihil imp..</p></div>
  </div>
  <div class="side-item">
    <div class="s-thumb"><div role="img" aria-label="Cross on a hill under a blue sky" style="background:linear-gradient(180deg,#2b4f8a,#8fb3d8 55%,#1a2230)"></div></div>
    <div><div class="side-title">Finibus bonorum et malorum</div>
    <div class="meta">&#128197; 25/11/2015 <i>|</i> &#128100; John <i>|</i> &#128172; 0 Comments</div>
    <p class="side-text">Nam libero tempore, cum soluta nobis est eligendi optio cumque nihil imp..</p></div>
  </div>
  <div class="side-item">
    <div class="s-thumb"><div role="img" aria-label="Folded hands holding a rosary" style="background:linear-gradient(135deg,#8a8f94,#d8b8a0 50%,#5a4a40)"></div></div>
    <div><div class="side-title">Finibus bonorum et malorum</div>
    <div class="meta">&#128197; 25/11/2015 <i>|</i> &#128100; John <i>|</i> &#128172; 0 Comments</div>
    <p class="side-text">Nam libero tempore, cum soluta nobis est eligendi optio cumque nihil imp..</p></div>
  </div>
  <div class="view-more"><u>View More</u> &gt;&gt;</div>

  <h2 class="section-title" style="margin-top:50px">Archive Posts</h2>
  <div class="archive-item"><div class="a-thumb"><div role="img" aria-label="Hands holding a rosary" style="background:linear-gradient(135deg,#8a8f94,#d8b8a0 50%,#5a4a40)"></div></div><div><div class="side-title">Finibus bonorum et malorum</div><div class="meta">&#128197; 25/11/2015 <i>|</i> &#128100; John <i>|</i> &#128172; 0 Comments</div></div></div>
  <div class="archive-item"><div class="a-thumb"><div role="img" aria-label="Cross against a golden sky" style="background:linear-gradient(180deg,#f2b24a,#c06a24 60%,#2a1408)"></div></div><div><div class="side-title">Finibus bonorum et malorum</div><div class="meta">&#128197; 25/11/2015 <i>|</i> &#128100; John <i>|</i> &#128172; 0 Comments</div></div></div>
  <div class="archive-item"><div class="a-thumb"><div role="img" aria-label="Woman in quiet prayer" style="background:linear-gradient(135deg,#e9e4df,#a89a8c 50%,#4a3a30)"></div></div><div><div class="side-title">Finibus bonorum et malorum</div><div class="meta">&#128197; 25/11/2015 <i>|</i> &#128100; John <i>|</i> &#128172; 0 Comments</div></div></div>
  <div class="archive-item"><div class="a-thumb"><div role="img" aria-label="Candle beside an open book" style="background:linear-gradient(135deg,#f3c46a,#a7652a 55%,#3d2310)"></div></div><div><div class="side-title">Finibus bonorum et malorum</div><div class="meta">&#128197; 25/11/2015 <i>|</i> &#128100; John <i>|</i> &#128172; 0 Comments</div></div></div>
  <div class="archive-item"><div class="a-thumb"><div role="img" aria-label="Small cross on a wooden surface" style="background:linear-gradient(135deg,#b88a6a,#7a4a30 55%,#d8c8b8)"></div></div><div><div class="side-title">Finibus bonorum et malorum</div><div class="meta">&#128197; 25/11/2015 <i>|</i> &#128100; John <i>|</i> &#128172; 0 Comments</div></div></div>
  <div class="view-more"><u>View More</u> &gt;&gt;</div>

  <h2 class="section-title" style="margin-top:32px">Newsletter Subscription</h2>
  <form class="newsletter">
    <div class="field">Name :</div>
    <div class="field">Email Address :</div>
    <span class="btn">Subscribe</span>
  </form>
</aside>

<footer class="site-footer">
  <div class="foot-links">Home<span>|</span>About us<span>|</span>Services<span>|</span>Blog<span>|</span>Events<span>|</span>Contact Us</div>
  <div class="copyright">&copy; Copyright 2015 My Pebble Porch Path. All rights reserved.</div>
  <div class="social" aria-label="Social links"><span></span><span></span><span></span><span></span></div>
</footer>
</body>
</html>
```